Mortgage Company ready to make a statement!

We have a basic logo that I am fairly happy with ... but it could use a little bit of tweaking before we order the sign for our building. We also want some knock-your-socks-off business cards.
Problem: Inside of our Mortgage Office (Bright Fern Mortgage Group), we are going to have a coffee lounge (Sunbrew Cafe) for Realtors to use instead of the local Cuppington to meet with homebuyers. The office and coffee lounge are in an industrial building and is decorated with cozy overstuffed chairs, a hodge podge of interesting lamps and furniture, and goal is to make it as inviting as possible. However, we are a financial institution... so we need to keep it pretty clean as well.
One of my favorite marketing ideas is to cut a house key for everyone who buys a home using us with a key that matches our logo. There's only one key shape that works really well, so that needs to match the logo in order for the idea to work. I'll attach an image of the key blank.... although the way the key hole cut out looks terrible, so I was thinking of having them just do a thin outline instead.
Would like a similar, matching logo for the Sunbrew Cafe... but possibly something that would be a little less formal and would be cute on a coffee mug- nothing stuffy.
AND, we're opening a home inspection company as well, and we would like that logo and branding to match. The home inspection company is "Bright Fern Home Inspections"
We were thinking that for the home inspection company , we could use a magnifying glass shape inside of the house shape for the logo, use a keyhole shape inside of the same house for the mortgage company, and use a coffee cup inside of the house shape for Sunbrew Cafe.
Just getting stuck and need to help. I designed the attached logo myself, and that is what we are currently using. Designers at local printing companies have failed to impress us.
The mortgage industry has a lot of numbers and logos, etc that they require us to put on our business cards... so it's hard to keep them looking clean.
HELP! HELP! :)

```html
<!DOCTYPE html>
<html lang="en">
<head>
<meta charset="utf-8">
<title>Bright Fern Mortgage Group – Business Cards</title>
<link href="https://fonts.googleapis.com/css2?family=Marcellus&family=Montserrat:wght@400;700&display=swap" rel="stylesheet">
<style>
  :root {
    --bg: #ece9e3;
    --brand-blue: #236584;
    --card-white: #ffffff;
    --ink: #3a3a3a;
    --shadow: rgba(0,0,0,0.22);
  }
  * { box-sizing: border-box; margin: 0; padding: 0; }
  html, body { width: 1200px; height: 929px; overflow: hidden; }
  body {
    background: var(--bg);
    display: flex;
    align-items: center;
    justify-content: center;
    gap: 44px;
  }
  .card {
    width: 530px;
    height: 303px;
    position: relative;
    overflow: hidden;
    box-shadow: 0 6px 14px var(--shadow);
  }
  .card--front { background: var(--brand-blue); display: flex; align-items: center; justify-content: center; }
  .card--back { background: var(--card-white); }

  .wordmark {
    display: flex;
    align-items: center;
    gap: 12px;
    font-family: "Marcellus", serif;
    font-weight: 400;
    line-height: 1;
  }
  .wordmark__dot { width: 14px; height: 14px; border-radius: 50%; flex: none; }
  .wordmark__text { display: flex; flex-direction: column; gap: 4px; }
  .wordmark__name { font-size: 40px; letter-spacing: 0.5px; white-space: nowrap; }
  .wordmark__sub { font-size: 22px; white-space: nowrap; }

  .card--front .wordmark { color: var(--card-white); }
  .card--front .wordmark__dot { background: var(--card-white); }
  .card--back .wordmark { color: var(--brand-blue); position: absolute; left: 30px; top: 132px; gap: 10px; }
  .card--back .wordmark__name { font-size: 28px; }
  .card--back .wordmark__sub { font-size: 15px; }
  .card--back .wordmark__dot { background: var(--brand-blue); width: 11px; height: 11px; }

  .divider {
    position: absolute;
    left: 250px; top: 58px;
    width: 2px; height: 146px;
    background: var(--brand-blue);
  }
  .contact {
    position: absolute;
    left: 266px; top: 48px;
    right: 16px;
    font-family: "Montserrat", sans-serif;
    color: var(--ink);
  }
  .contact__name {
    font-family: "Marcellus", serif;
    color: var(--brand-blue);
    font-size: 23px;
    letter-spacing: 0.5px;
    white-space: nowrap;
  }
  .contact__title { font-weight: 700; font-size: 14px; margin: 4px 0 12px 10px; }
  .contact__address { font-size: 11.5px; line-height: 1.35; letter-spacing: 0.5px; margin: 0 0 8px 10px; }
  .contact__list { list-style: none; font-size: 11.5px; letter-spacing: 0.4px; margin-left: 10px; }
  .contact__list li { display: flex; align-items: center; gap: 8px; line-height: 1.5; white-space: nowrap; }
  .contact__list svg { width: 10px; height: 10px; flex: none; fill: var(--brand-blue); }
</style>
</head>
<body>
  <section class="card card--front" aria-label="Card front">
    <div class="wordmark">
      <span class="wordmark__dot"></span>
      <div class="wordmark__text">
        <span class="wordmark__name">BRIGHT FERN</span>
        <span class="wordmark__sub">Mortgage Group</span>
      </div>
    </div>
  </section>

  <section class="card card--back" aria-label="Card back">
    <div class="wordmark">
      <span class="wordmark__dot"></span>
      <div class="wordmark__text">
        <span class="wordmark__name">BRIGHT FERN</span>
        <span class="wordmark__sub">Mortgage Group</span>
      </div>
    </div>
    <div class="divider"></div>
    <div class="contact">
      <p class="contact__name">DANA WHITLOW</p>
      <p class="contact__title">CEO</p>
      <p class="contact__address">Harbor Plaza<br>Northgate City</p>
      <ul class="contact__list">
        <li><svg viewBox="0 0 10 10"><rect x="2.5" y="0.5" width="5" height="9" rx="1" fill="none" stroke="#236584" stroke-width="1"/></svg>000-555-0142</li>
        <li><svg viewBox="0 0 10 10"><rect x="2.5" y="0" width="5" height="3"/><rect x="0.5" y="3.5" width="9" height="4" rx="1"/><rect x="2.5" y="7" width="5" height="3"/></svg>000-555-0143</li>
        <li><svg viewBox="0 0 10 10"><path d="M0 2h10v6H0z"/><path d="M0 2l5 3.5L10 2" fill="none" stroke="#fff" stroke-width="0.8"/></svg>dana.whitlow@brightfern.com</li>
      </ul>
    </div>
  </section>
</body>
</html>
```